I need an Office Furniture selling website

My office furniture store is driven by creativity and innovation. With this i am searching for an industry standard website for my office furniture and items selling website. I sell a wide range of office furniture items such as chairs, tables, burglary, cotton, wardrobe, etc. There will be a category for each of the items i sell. My business is based in the United States and services only US based residents. I don't accept online payments and customers are to pay on delivery of items. The website is to have images of the items i sell. I would like brown, black and golden colors because those are the colors furniture mostly make use of. Designs submitted should be unique.

Industry/Entity Type

Furniture Store

Coding

Coded - Design and coding required

```html
<!DOCTYPE html>
<html lang="en">
<head>
<meta charset="utf-8">
<title>Office Furniture</title>
<link href="https://fonts.googleapis.com/css2?family=Roboto:wght@300;400;500;700&display=swap" rel="stylesheet">
<style>
:root{
  --gold:#b69c3f;
  --ink:#1f1f1f;
  --text:#6b6b6b;
  --muted:#8a8a8a;
  --hero:#e9e8e3;
  --band:#efefed;
  --tile:#f0f0f0;
  --footer:#ececea;
  --white:#ffffff;
  --line:#d8d8d8;
}
*{margin:0;padding:0;box-sizing:border-box}
html,body{width:1200px;height:2995px;overflow:hidden;background:var(--white)}
body{position:relative;font-family:"Roboto",Arial,sans-serif;color:var(--ink)}
.abs{position:absolute}
.gold{color:var(--gold)}
.btn{position:absolute;display:flex;align-items:center;justify-content:center;background:var(--gold);color:var(--white);font:500 19px "Roboto",sans-serif;letter-spacing:.3px;text-transform:uppercase}
.btn-outline{background:transparent;color:var(--gold);border:2px solid var(--gold)}
.photo{position:absolute}

/* header */
.brand-name{left:78px;top:40px;font:400 30px/1 "Roboto",sans-serif;letter-spacing:1px;color:var(--ink);text-transform:uppercase}
.nav{left:442px;top:32px;display:flex;height:54px;align-items:center;font:400 16px "Roboto",sans-serif;color:#333;text-transform:uppercase}
.nav a{color:inherit;text-decoration:none;margin-right:38px}
.nav .active{background:var(--gold);color:var(--white);padding:0 22px;height:54px;display:flex;align-items:center;margin-right:26px}

/* hero */
.hero{left:0;top:115px;width:1200px;height:563px;background:var(--hero)}
.hero-arrow{position:absolute;top:256px;width:48px;height:48px}
.hero-title{left:616px;top:142px;font:500 62px/1 "Roboto",sans-serif;letter-spacing:1px}
.hero-text{left:624px;top:234px;width:510px;font:400 14px/25px "Roboto",sans-serif;color:var(--muted)}

/* works */
.work{top:742px;width:332px;height:208px}
.work-label{left:434px;top:742px;width:332px;height:208px;display:flex;flex-direction:column;align-items:center;justify-content:center}
.work-label p{font:400 23px "Roboto",sans-serif;color:#333;margin-bottom:14px}

/* welcome */
.welcome{left:0;top:1012px;width:1200px;height:416px;background:var(--band)}
.section-title{font:400 41px/1 "Roboto",sans-serif;text-transform:uppercase;color:var(--ink)}
.welcome-text{left:78px;top:1130px;width:690px;font:400 14px/26px "Roboto",sans-serif;color:#555}
.welcome-text p{margin-bottom:6px}

/* products */
.card{position:absolute;width:250px;height:310px;background:var(--tile)}
.card .pic{position:absolute;left:0;top:0;width:250px;height:228px}
.card .name{position:absolute;left:6px;top:238px;font:400 25px/1 "Roboto",sans-serif;color:var(--ink)}
.card .price{position:absolute;left:6px;top:272px;font:400 17px/1 "Roboto",sans-serif;color:var(--gold)}
.card .btn{left:130px;top:242px;width:120px;height:56px}
.card.raised{background:var(--white);box-shadow:0 2px 10px rgba(0,0,0,.15)}
.card.raised .pic{left:10px;top:10px;width:230px;height:208px;background:var(--tile)}

/* news */
.news-date{width:50px;height:52px;border:1px solid var(--gold);display:flex;align-items:center;justify-content:center;font:400 22px "Roboto",sans-serif;color:#333}
.news-meta{font:400 15px/1 "Roboto",sans-serif;color:var(--gold)}
.news-head{font:400 15px/1 "Roboto",sans-serif;color:#222;text-transform:uppercase}
.news-text{width:270px;font:400 14px/25px "Roboto",sans-serif;color:var(--muted)}

/* footer */
.footer{left:0;top:2634px;width:1200px;height:361px;background:var(--footer)}
.subscribe{left:78px;top:2586px;width:1044px;height:104px;background:var(--white);box-shadow:0 2px 10px rgba(0,0,0,.12)}
.foot-head{font:700 15px/1 "Roboto",sans-serif;color:var(--gold);text-transform:uppercase;letter-spacing:.3px}
.foot-list{list-style:none;font:400 14px/23px "Roboto",sans-serif;color:#555}
.foot-list li{position:relative;padding-left:16px}
.foot-list li::before{content:"";position:absolute;left:0;top:8px;width:5px;height:5px;border-top:1.5px solid var(--gold);border-right:1.5px solid var(--gold);transform:rotate(45deg)}
.contact-row{display:flex;align-items:flex-start;gap:16px;font:400 14px/1 "Roboto",sans-serif;color:#555}
.contact-row svg{flex:none}
.foot-brand{left:900px;top:2770px;width:222px;text-align:center;font:500 18px/1 "Roboto",sans-serif;color:var(--ink)}
.copyright{left:0;top:2958px;width:1200px;text-align:center;font:400 14px "Roboto",sans-serif;color:#555}
</style>
</head>
<body>

<!-- header -->
<div class="abs brand-name">Office Furniture</div>
<nav class="abs nav">
  <a class="active" href="#">Home</a>
  <a href="#">About Us</a>
  <a href="#">Product</a>
  <a href="#">Free Estimate</a>
  <a href="#">News</a>
  <a href="#">Contact Us</a>
</nav>

<!-- hero -->
<section class="abs hero">
  <svg class="hero-arrow" style="left:16px" viewBox="0 0 48 48"><circle cx="24" cy="24" r="22" fill="none" stroke="#9a9a9a" stroke-width="1.5"/><path d="M27 16l-8 8 8 8" fill="none" stroke="#9a9a9a" stroke-width="2"/></svg>
  <svg class="hero-arrow" style="left:1136px" viewBox="0 0 48 48"><circle cx="24" cy="24" r="22" fill="none" stroke="#9a9a9a" stroke-width="1.5"/><path d="M21 16l8 8-8 8" fill="none" stroke="#9a9a9a" stroke-width="2"/></svg>
  <div class="photo" role="img" aria-label="Brown leather egg lounge chair with matching footstool" style="left:76px;top:90px;width:484px;height:410px;background:radial-gradient(ellipse at 40% 40%,#6a3a25 0%,#4a2618 45%,rgba(233,232,227,0) 72%)"></div>
  <h1 class="abs hero-title"><span class="gold">O</span>ffice <span class="gold">f</span>urniture</h1>
  <p class="abs hero-text">Lorem Ipsum is simply dummy text of the printing and typesetting indu - stry. Lorem Ipsum has been the industry's standard dummy text ever since the 1500s, when an unknown printer.</p>
  <a class="btn" style="left:624px;top:329px;width:198px;height:62px">Know More</a>
  <a class="btn btn-outline" style="left:832px;top:329px;width:192px;height:62px">Contact Us</a>
</section>

<!-- latest work -->
<div class="photo work" role="img" aria-label="Bright open-plan office with glass partitions" style="left:78px;background:linear-gradient(135deg,#dfe4e8,#f4f6f7 50%,#c9d1d6)"></div>
<div class="photo work" role="img" aria-label="Warm office desk with plant, gold toned" style="left:434px;background:linear-gradient(135deg,#d7cc94,#e6dca8 50%,#cbbd7c)"></div>
<div class="abs work-label">
  <p>LATEST WORK</p>
  <a class="btn" style="position:static;width:106px;height:50px">View</a>
</div>
<div class="photo work" role="img" aria-label="Reception area with curved front desk" style="left:790px;background:linear-gradient(180deg,#eeeeec,#dcdcd8 60%,#b8b3ab)"></div>

<!-- welcome -->
<section class="abs welcome">
  <div class="photo" role="img" aria-label="White office storage units with orange glass panels" style="left:780px;top:0;width:420px;height:416px;background:linear-gradient(180deg,#e6e6e4 0%,#d9a36b 40%,#e0e0de 60%,#f2f2f0 100%)"></div>
</section>
<h2 class="abs section-title" style="left:78px;top:1075px"><span class="gold">W</span>ELCOME TO <span class="gold">O</span>FFICE FURNITURE</h2>
<div class="abs welcome-text">
  <p>Lorem Ipsum is simply dummy text of the printing and typesetting industry. Lorem Ipsum has been the industry's standard dummy text ever since the 1500s, when an unknown printer took a galley of type and scrambled it to make a type specimen book. It has survived not only five centuries, but also the leap into electronic. industry's standard dummy text ever since.</p>
  <p>Lorem Ipsum is simply dummy text of the printing and typesetting industry. Lorem Ipsum has been the industry's standard dummy text ever since the 1500s.</p>
</div>
<a class="btn" style="left:78px;top:1314px;width:176px;height:62px">Know More</a>

<!-- products -->
<h2 class="abs section-title" style="left:0;width:1200px;top:1495px;text-align:center"><span class="gold">O</span>UR <span class="gold">P</span>RODUCT</h2>

<div class="card" style="left:78px;top:1560px"><div class="pic" role="img" aria-label="Black cantilever chair" style="background:radial-gradient(circle at 50% 50%,#2a2a2a 0,#2a2a2a 18%,var(--tile) 40%)"></div><div class="name">Chairs</div><div class="price">$25.89</div><a class="btn">Detail</a></div>
<div class="card" style="left:344px;top:1560px"><div class="pic" role="img" aria-label="Stack of folded coloured cotton blankets" style="background:radial-gradient(circle at 50% 50%,#b24a3a 0,#3b6fa0 18%,var(--tile) 42%)"></div><div class="name">Cotton</div><div class="price">$25.89</div><a class="btn">Detail</a></div>
<div class="card raised" style="left:602px;top:1560px;width:260px;height:314px"><div class="pic" role="img" aria-label="Black steel safe with open door" style="background:radial-gradient(circle at 50% 50%,#222 0,#222 20%,var(--tile) 40%)"></div><div class="name" style="left:16px;top:240px">Burglary</div><div class="price" style="left:16px">$25.89</div><a class="btn" style="left:130px;top:242px">Detail</a></div>
<div class="card" style="left:874px;top:1560px"><div class="pic" role="img" aria-label="Dark curved side table" style="background:radial-gradient(circle at 50% 50%,#2b2522 0,#2b2522 17%,var(--tile) 40%)"></div><div class="name">Table</div><div class="price">$25.89</div><a class="btn">Detail</a></div>

<div class="card" style="left:78px;top:1904px"><div class="pic" role="img" aria-label="Black chair with carved back" style="background:radial-gradient(circle at 50% 50%,#1e1e1e 0,#1e1e1e 17%,var(--tile) 40%)"></div><div class="name">Chairs</div><div class="price">$25.89</div><a class="btn">Detail</a></div>
<div class="card" style="left:344px;top:1904px"><div class="pic" role="img" aria-label="Folded white cotton throw" style="background:radial-gradient(circle at 50% 50%,#cfcfca 0,#dadad6 22%,var(--tile) 42%)"></div><div class="name">Cotton</div><div class="price">$25.89</div><a class="btn">Detail</a></div>
<div class="card" style="left:610px;top:1904px"><div class="pic" role="img" aria-label="Dark wooden wardrobe" style="background:linear-gradient(90deg,var(--tile) 32%,#3a2a22 32%,#3a2a22 65%,var(--tile) 65%) center/100% 66% no-repeat,var(--tile)"></div><div class="name">Wardrobe</div><div class="price">$25.89</div><a class="btn">Detail</a></div>
<div class="card" style="left:874px;top:1904px"><div class="pic" role="img" aria-label="Black round pedestal table" style="background:radial-gradient(ellipse at 50% 45%,#1c1c1c 0,#1c1c1c 22%,var(--tile) 45%)"></div><div class="name">Table</div><div class="price">$25.89</div><a class="btn">Detail</a></div>

<!-- news -->
<h2 class="abs section-title" style="left:0;width:1200px;top:2282px;text-align:center"><span class="gold">L</span>ATEST <span class="gold">N</span>EWS</h2>

<article>
  <div class="abs news-date" style="left:78px;top:2354px">11</div>
  <div class="abs news-meta" style="left:140px;top:2358px">Aug, 2016</div>
  <div class="abs news-head" style="left:140px;top:2388px">Lorem Ipsum is simple text</div>
  <p class="abs news-text" style="left:78px;top:2422px">Lorem Ipsum is simply dummy text of the printing and typesetting industry has been the industry's standard dummy text ever since the 1500s.</p>
  <div class="photo" role="img" aria-label="Executive office with dark wooden desk" style="left:372px;top:2356px;width:220px;height:168px;background:linear-gradient(180deg,#e4e2de 0%,#cfc9c2 45%,#5a3d30 70%,#8d7e74 100%)"></div>
</article>
<article>
  <div class="abs news-date" style="left:610px;top:2354px">11</div>
  <div class="abs news-meta" style="left:672px;top:2358px">Aug, 2016</div>
  <div class="abs news-head" style="left:672px;top:2388px">Lorem Ipsum is simple text</div>
  <p class="abs news-text" style="left:610px;top:2422px">Lorem Ipsum is simply dummy text of the printing and typesetting industry has been the industry's standard dummy text ever since the 1500s.</p>
  <div class="photo" role="img" aria-label="Bright lounge with black chairs" style="left:904px;top:2356px;width:220px;height:168px;background:linear-gradient(180deg,#f1f3f4 0%,#dde2e5 50%,#4a4d50 75%,#c9cdd0 100%)"></div>
</article>

<!-- footer -->
<section class="abs footer"></section>
<div class="abs subscribe">
  <div class="abs" style="left:90px;top:46px;font:400 14px 'Roboto',sans-serif;color:#777">Enter Your Email</div>
  <div class="abs" style="left:82px;top:82px;width:652px;height:1px;background:#999"></div>
  <a class="btn" style="left:756px;top:20px;width:208px;height:62px">Subscribe</a>
</div>

<div class="abs foot-head" style="left:80px;top:2730px">Usefull Links</div>
<ul class="abs foot-list" style="left:78px;top:2768px">
  <li>Homel</li><li>About Us</li><li>Product</li><li>Free Estimate</li><li>News</li><li>Contact Us</li>
</ul>

<div class="abs foot-head" style="left:344px;top:2730px">Our Product</div>
<ul class="abs foot-list" style="left:344px;top:2768px">
  <li>Chairs</li><li>Tables</li><li>Burglary</li><li>Cotton</li><li>Wardrobe</li>
</ul>

<div class="abs foot-head" style="left:610px;top:2730px">Get In Touch</div>
<div class="abs" style="left:608px;top:2764px;display:flex;flex-direction:column;gap:14px">
  <div class="contact-row">
    <svg width="16" height="20" viewBox="0 0 16 20"><path d="M8 1a6 6 0 0 0-6 6c0 4.5 6 12 6 12s6-7.5 6-12a6 6 0 0 0-6-6z" fill="none" stroke="var(--gold)" stroke-width="1.4"/><circle cx="8" cy="7" r="2.2" fill="none" stroke="var(--gold)" stroke-width="1.4"/></svg>
    <div><div style="font-size:15px;color:#333;letter-spacing:.3px">OFFICE FURNITURE</div><div style="margin-top:8px">Lorem ipsum dolor amet simple.</div></div>
  </div>
  <div class="contact-row">
    <svg width="16" height="16" viewBox="0 0 16 16"><path d="M3 1.5l3 3-1.6 2a9 9 0 0 0 5 5l2-1.6 3 3-2 2C6 15 1 10 1.5 3.5z" fill="none" stroke="var(--gold)" stroke-width="1.3"/></svg>
    <div>+(1) 555 014 2290</div>
  </div>
  <div class="contact-row">
    <svg width="16" height="16" viewBox="0 0 16 16"><rect x="1.5" y="5" width="13" height="8" rx="1.5" fill="none" stroke="var(--gold)" stroke-width="1.3"/><rect x="4" y="1.5" width="8" height="4" fill="none" stroke="var(--gold)" stroke-width="1.3"/><path d="M4 10h8" stroke="var(--gold)" stroke-width="1.3"/></svg>
    <div>+(1) 555 014 2290</div>
  </div>
  <div class="contact-row">
    <svg width="16" height="14" viewBox="0 0 16 14"><rect x="1" y="1.5" width="14" height="11" fill="none" stroke="var(--gold)" stroke-width="1.3"/><path d="M1 2l7 6 7-6" fill="none" stroke="var(--gold)" stroke-width="1.3"/></svg>
    <div>hello@deskandoakstudio.com</div>
  </div>
</div>

<div class="abs foot-brand">Office Furniture</div>
<div class="abs" style="left:900px;top:2856px;width:222px;height:1px;background:var(--line)"></div>
<svg class="abs" style="left:932px;top:2862px" width="146" height="44" viewBox="0 0 146 44" aria-label="Social links">
  <circle cx="22" cy="22" r="20" fill="var(--gold)"/>
  <circle cx="73" cy="22" r="19" fill="none" stroke="var(--gold)" stroke-width="1.5"/>
  <circle cx="124" cy="22" r="19" fill="none" stroke="var(--gold)" stroke-width="1.5"/>
</svg>

<div class="abs" style="left:304px;top:2932px;width:592px;height:1px;background:var(--line)"></div>
<div class="abs copyright">© 2016 <span class="gold">Office Furniture</span> - All rights reserved.</div>

</body>
</html>
```